Indy Film Production Company/Studio

We need a business card designed from an existing logo. We are a digital studio/production company that caters to creating genre entertainment, like Action, Horror, and martial arts. The card along with the logo will be used to Brand the company from letter heads to banners. The design will also be used for postcards and Brochures. It should be professional and masculine.
Updates

Thank you to all the designers who have participated. I'm narrowing down who it will be. Thank you again.

Target Market(s)

Investors, Networks, Producers, and actors

Industry/Entity Type

Film Production

Contact Information for Business Card

Teodoro Valbuena
Producer/Writer/Director
www.kestrelpicturehouse.example

Requirements
Must have
• Website address, Facebook icon and Twitter icon possibly in the back of the card.
Nice to have
• Logline of Company: Follow The Action.

```html
<!DOCTYPE html>
<html lang="en">
<head>
<meta charset="utf-8">
<title>Kestrel Picture House – Business Card</title>
<link rel="stylesheet" href="https://fonts.googleapis.com/css2?family=Roboto:wght@400;900&display=swap">
<style>
  :root {
    --backdrop: #e9e6e1;
    --card-dark: #3a3a3b;
    --card-light: #ffffff;
    --brand-red: #e8232b;
    --ink: #3b3b3b;
    --ink-soft: #5a5a5a;
    --on-dark: #f4f4f4;
  }
  * { box-sizing: border-box; margin: 0; padding: 0; }
  html, body {
    width: 1200px; height: 950px; overflow: hidden;
    background: var(--backdrop);
    font-family: "Roboto", Arial, sans-serif;
  }
  .canvas { position: relative; width: 1200px; height: 950px; }
  .card {
    position: absolute; width: 560px; height: 320px;
    border-radius: 4px; overflow: hidden;
    box-shadow: 0 10px 24px rgba(0,0,0,0.22);
  }
  .card-back { left: 90px; top: 110px; background: var(--card-dark); }
  .card-front { left: 550px; top: 520px; background: var(--card-light); }

  .social-links { position: absolute; top: 16px; right: 18px; display: flex; gap: 4px; }
  .social-square { width: 20px; height: 20px; background: var(--on-dark); border-radius: 2px; }

  .wordmark { font-weight: 900; text-transform: uppercase; line-height: 0.95; letter-spacing: 1px; }
  .card-back .wordmark {
    position: absolute; left: 0; right: 0; top: 92px; text-align: center;
    color: var(--on-dark); font-size: 44px;
  }
  .back-website {
    position: absolute; left: 0; right: 0; top: 236px; text-align: center;
    color: var(--on-dark); font-size: 15px; letter-spacing: 2px;
  }

  .corner-accents { position: absolute; inset: 0; }
  .card-front .wordmark {
    position: absolute; right: 30px; top: 28px; text-align: right;
    color: var(--brand-red); font-size: 32px;
  }
  .holder { position: absolute; left: 40px; top: 170px; }
  .holder-name { color: var(--brand-red); font-size: 22px; font-weight: 400; }
  .holder-role { color: var(--ink); font-size: 15px; margin-top: 4px; }
  .contact-list { list-style: none; margin-top: 16px; }
  .contact-item {
    display: flex; align-items: center; gap: 9px;
    color: var(--ink-soft); font-size: 14px; line-height: 21px;
  }
  .contact-icon { width: 13px; height: 13px; flex: none; }
</style>
</head>
<body>
<main class="canvas">

  <section class="card card-back" aria-label="Card back">
    <div class="social-links">
      <span class="social-square"></span>
      <span class="social-square"></span>
    </div>
    <div class="wordmark">Kestrel<br>Picture House</div>
    <p class="back-website">www.kestrelpicturehouse.example</p>
  </section>

  <section class="card card-front" aria-label="Card front">
    <svg class="corner-accents" width="560" height="320" viewBox="0 0 560 320" aria-hidden="true">
      <polygon points="0,0 95,0 0,150" fill="var(--brand-red)"/>
      <polygon points="560,130 560,320 455,320" fill="var(--brand-red)"/>
    </svg>
    <div class="wordmark">Kestrel<br>Picture House</div>

    <div class="holder">
      <h1 class="holder-name">Teodoro Valbuena</h1>
      <p class="holder-role">Producer/Writer/Director</p>
      <ul class="contact-list">
        <li class="contact-item">
          <svg class="contact-icon" viewBox="0 0 16 16" aria-hidden="true">
            <path fill="var(--brand-red)" d="M3.5 1.5l2.5 0 1 3.5-1.6 1.2a9 9 0 0 0 4.4 4.4L11 9l3.5 1v2.5a2 2 0 0 1-2 2A11 11 0 0 1 1.5 3.5a2 2 0 0 1 2-2z"/>
          </svg>
          555 0142 7781
        </li>
        <li class="contact-item">
          <svg class="contact-icon" viewBox="0 0 16 16" aria-hidden="true">
            <rect x="1" y="3" width="14" height="10" rx="1" fill="var(--brand-red)"/>
            <path d="M1.5 3.8L8 9l6.5-5.2" fill="none" stroke="#fff" stroke-width="1.3"/>
          </svg>
          teo@kestrelpicturehouse.example
        </li>
        <li class="contact-item">
          <svg class="contact-icon" viewBox="0 0 16 16" aria-hidden="true">
            <circle cx="8" cy="8" r="7" fill="var(--brand-red)"/>
            <path d="M1.5 8h13M8 1.2c2.4 2 2.4 11.6 0 13.6M8 1.2c-2.4 2-2.4 11.6 0 13.6" fill="none" stroke="#fff" stroke-width="1"/>
          </svg>
          www.kestrelpicturehouse.example
        </li>
      </ul>
    </div>
  </section>

</main>
</body>
</html>
```